Tallowick Haul Away Start-Up Flyer

My company provides junk removal and small demolition services. I need a flyer that is modern, simple but catches the eye. Clearly shows what my company is about. I provided two uploaded files, one with out logo and the other with the logo and slogan. I would like the flyer size to be a full page (8.5"x10.98"). I also provided a list of services my company offers. I would like to incorporate a $50 Coupon for Junk Removal Service and $100 Coupon for Demolition Service at the bottom of the flyer. These flyers will be the first mailed out and be my initial entry into the market. Thank you for your time.
Target Market(s)
Home owners, Contractors, ages 30-65
Industry/Entity Type
Junk Removal
Requirements
Must have
- The company website, www.TallowickHaulAway.example
- Address: PO BOX 574 Dellmont Falls, NY 10482
- Phone Number: (555) 284-6170
- Email: TallowickHaulAway@mailbox.example
- Must be a full page size, coupons mentioned above, company logo and slogan. Clearly show what the company does in a clean, modern, eye poping way.
- Must state that the company is veteran owned and operated, a small picture or graphic on the bottom would be fine. Below is a list of all services offered that must be on flyer:
- JUNK REMOVAL SERVICES:
- CONCRETE REMOVAL
- DEMOLITION REMOVAL
- APPLIANCE REMOVAL
- CARPET REMOVAL
- COMPUTER RECYCLING
- CONSTRUCTION CLEANOUT
- DUMPSTER ALTERNATIVE
- ESTATE CLEANOUT
- BASEMENT CLEANOUT
- GARAGE CLEANOUT
- ATTIC CLEANOUT
- STORAGE UNIT CLEANOUT
- FURNITURE REMOVAL
- GARBAGE REMOVAL ALTERNATIVE
- LEAF REMOVAL
- MATTRESS REMOVAL
- MONITOR RECYLING
- PRINTER RECYLING
- RUBBISH REMOVAL
- REFRIGERATOR REMOVAL
- TRASH REMOVAL
- TV RECYCLE
- TIRE RECYCLE
- *no hazerdous material
- DEMOLITION SERVICES:
- SHED RIP OUT & REMOVAL
- KITCHEN RIP OUT & REMOVAL
- BATHROOM RIP OUT & REMOVAL
- WHOLE HOUSE RIP OUT & REMOVAL
- DECK REMOVAL
- HOT TUB REMOVAL
- POOL REMOVAL
- RENOVATION PREP RIP OUTS
- *no whole house knock downs
- RESIDENTIAL:
- PLOW DRIVEWAYS
- SHOVEL OUT STAIRWAYS
- SNOW BLOW WALKWAYS/PATHS
- SALT SPREAD DRIVEWAYS/ WALKWAYS/ PATHS/ STAIRS
Nice to have
- It would be nice if the color scheme incorparated colors from my bussiness cards. I upladed a picture of one of them as a reference. As far as colors, I am a fan of any and all earth tones.

```html
<!DOCTYPE html>
<html lang="en">
<head>
<meta charset="utf-8">
<title>Tallowick Haul Away – Flyer</title>
<link href="https://fonts.googleapis.com/css2?family=Oswald:wght@500;600;700&family=Roboto+Condensed:ital,wght@0,400;0,700;1,700&display=swap" rel="stylesheet">
<style>
  :root{
    --blue:#1f5fa8;
    --blue-dark:#123f78;
    --red:#e3262b;
    --green:#17a35a;
    --ink:#2a2a2a;
    --grey:#8a8f94;
    --paper:#ffffff;
    --photo-a:#b9cfe3;
    --photo-b:#8a7a62;
  }
  *{margin:0;padding:0;box-sizing:border-box}
  html,body{width:900px;height:1200px;overflow:hidden;background:var(--paper)}
  .flyer{position:relative;width:900px;height:1200px;background:var(--paper);font-family:"Roboto Condensed",Arial,sans-serif;color:var(--ink);overflow:hidden}
  .hero-photo,.hero-swoosh{position:absolute;left:0;top:0}

  .brand{position:absolute;left:590px;top:30px;display:flex;align-items:center;gap:10px;white-space:nowrap}
  .brand-dot{width:36px;height:36px;border-radius:50%;background:var(--red);flex:none}
  .brand-name{font-family:"Oswald",Arial,sans-serif;font-weight:600;font-size:26px;line-height:1;color:var(--blue)}

  .headline{position:absolute;left:38px;top:482px;font-family:"Oswald",Arial,sans-serif;font-weight:700;text-transform:uppercase;line-height:1;white-space:nowrap}
  .headline-main{font-size:64px;color:var(--blue)}
  .headline-sub{font-size:40px;color:var(--red);margin-top:4px;letter-spacing:.5px}

  .veteran-badge{position:absolute;left:660px;top:484px;width:210px;height:96px;border:4px solid var(--grey);border-radius:10px;display:flex;align-items:center;justify-content:center;gap:12px;color:var(--grey)}
  .veteran-star{width:36px;height:36px}
  .veteran-text{font-family:"Oswald",Arial,sans-serif;font-weight:600;font-size:20px;line-height:1.05;text-transform:uppercase}

  .section-bar{position:absolute;height:34px;color:#fff;font-style:italic;font-weight:700;font-size:19px;line-height:34px;text-transform:uppercase;white-space:nowrap}
  .bar-junk{left:0;top:604px;width:600px;background:var(--green);padding-left:40px}
  .bar-demo{left:630px;top:604px;width:270px;background:var(--blue);padding-left:14px}
  .bar-home{left:630px;top:826px;width:270px;background:var(--blue);padding-left:14px}

  .service-list{position:absolute;list-style:none}
  .service-list li{font-size:16px;line-height:19px;padding-left:16px;position:relative}
  .service-list li::before{content:"";position:absolute;left:2px;top:7px;width:7px;height:7px;border-radius:50%;background:var(--red)}
  .service-list li.note{font-style:italic;font-weight:700;color:var(--red)}
  .service-list li.note::before{display:none}
  .list-junk{left:40px;top:648px;width:560px;display:grid;grid-template-columns:1fr 1fr;grid-template-rows:repeat(12,19px);grid-auto-flow:column;column-gap:16px}
  .list-demo{left:636px;top:646px;width:260px}
  .list-home{left:636px;top:868px;width:260px}

  .coupon{position:absolute;top:972px;width:270px;height:96px;border-radius:10px;color:#fff;display:flex;flex-direction:column;align-items:center;justify-content:center;outline:3px dashed #fff;outline-offset:-8px}
  .coupon-50{left:30px;background:var(--blue)}
  .coupon-100{left:315px;background:var(--red)}
  .coupon-amount{font-family:"Oswald",Arial,sans-serif;font-weight:700;font-size:50px;line-height:1}
  .coupon-label{font-family:"Oswald",Arial,sans-serif;font-weight:600;font-size:17px;line-height:1;margin-top:4px;text-transform:uppercase;white-space:nowrap}

  .contact{position:absolute;left:608px;top:966px;width:285px;white-space:nowrap}
  .contact-call{font-family:"Oswald",Arial,sans-serif;font-weight:700;font-size:28px;color:var(--blue-dark);line-height:1.05;text-transform:uppercase}
  .contact-phone{font-family:"Oswald",Arial,sans-serif;font-weight:700;font-size:24px;color:var(--red);line-height:1.2}
  .contact-line{font-size:15px;line-height:19px;color:var(--ink)}

  .footer{position:absolute;left:0;top:1078px}
  .footer-url{position:absolute;left:0;top:1122px;width:900px;text-align:center;color:#fff;font-style:italic;font-weight:700;font-size:38px;letter-spacing:.5px;white-space:nowrap}
</style>
</head>
<body>
<main class="flyer">
  <svg class="hero-photo" width="900" height="470" role="img" aria-label="Photo of a construction worker in a hard hat laying paving stones with an excavator behind">
    <defs>
      <linearGradient id="photoTone" x1="0" y1="0" x2="0" y2="1">
        <stop offset="0" stop-color="var(--photo-a)"/>
        <stop offset=".55" stop-color="#c9c3b3"/>
        <stop offset="1" stop-color="var(--photo-b)"/>
      </linearGradient>
    </defs>
    <path d="M0,0 H470 C530,120 650,205 900,215 V370 C700,420 400,435 0,440 Z" fill="url(#photoTone)"/>
  </svg>

  <svg class="hero-swoosh" width="900" height="480" aria-hidden="true">
    <path d="M462,0 C522,125 645,212 900,222" fill="none" stroke="var(--red)" stroke-width="16"/>
    <path d="M448,0 C508,140 640,232 900,242" fill="none" stroke="var(--green)" stroke-width="4"/>
    <path d="M0,440 C400,435 700,420 900,370 V398 C700,448 400,465 0,468 Z" fill="var(--red)"/>
    <path d="M0,472 C400,469 700,457 900,407" fill="none" stroke="var(--green)" stroke-width="4"/>
  </svg>

  <div class="brand">
    <span class="brand-dot"></span>
    <span class="brand-name">Tallowick Haul Away</span>
  </div>

  <h1 class="headline">
    <div class="headline-main">Simple Sensible</div>
    <div class="headline-sub">Setting the Standard</div>
  </h1>

  <div class="veteran-badge">
    <svg class="veteran-star" viewBox="0 0 40 40" aria-hidden="true"><polygon points="20,2 25,15 39,15 28,24 32,38 20,30 8,38 12,24 1,15 15,15" fill="var(--grey)"/></svg>
    <div class="veteran-text">Veteran<br>Owned &amp;<br>Operated</div>
  </div>

  <div class="section-bar bar-junk">Junk removal services we provide:</div>
  <ul class="service-list list-junk">
    <li>Concrete removal</li><li>Demolition removal</li><li>Appliance removal</li>
    <li>Carpet removal</li><li>Computer recycling</li><li>Construction cleanout</li>
    <li>Dumpster alternative</li><li>Estate cleanout</li><li>Basement cleanout</li>
    <li>Garage cleanout</li><li>Attic cleanout</li><li>Storage unit cleanout</li>
    <li>Furniture removal</li><li>Garbage removal alternative</li><li>Leaf removal</li>
    <li>Mattress removal</li><li>Monitor recycling</li><li>Printer recycling</li>
    <li>Rubbish removal</li><li>Refrigerator removal</li><li>Trash removal</li>
    <li>TV recycle</li><li>Tire recycle</li><li class="note">*No hazardous material</li>
  </ul>

  <div class="section-bar bar-demo">Demolition services:</div>
  <ul class="service-list list-demo">
    <li>Shed rip out &amp; removal</li>
    <li>Kitchen rip out &amp; removal</li>
    <li>Bathroom rip out &amp; removal</li>
    <li>Whole house rip out &amp; removal</li>
    <li>Deck removal</li>
    <li>Hot tub removal</li>
    <li>Pool removal</li>
    <li>Renovation prep rip outs</li>
    <li class="note">*No whole house knock downs</li>
  </ul>

  <div class="section-bar bar-home">Residential:</div>
  <ul class="service-list list-home">
    <li>Plow driveways</li>
    <li>Shovel out stairways</li>
    <li>Snow blow walkways/paths</li>
    <li>Salt spread driveways/ walkways/ paths/ stairs</li>
  </ul>

  <div class="coupon coupon-50">
    <span class="coupon-amount">$50</span>
    <span class="coupon-label">Junk Removal Service</span>
  </div>
  <div class="coupon coupon-100">
    <span class="coupon-amount">$100</span>
    <span class="coupon-label">Demolition Service</span>
  </div>

  <div class="contact">
    <div class="contact-call">Contact us now!</div>
    <div class="contact-phone">At : (555) 284-6170</div>
    <div class="contact-line">TallowickHaulAway@mailbox.example</div>
    <div class="contact-line">PO BOX 574 Dellmont Falls, NY 10482</div>
  </div>

  <svg class="footer" width="900" height="122" aria-hidden="true">
    <path d="M0,26 C300,10 600,5 900,0 V122 H0 Z" fill="var(--green)"/>
    <path d="M0,34 C300,18 600,13 900,8 V122 H0 Z" fill="var(--red)"/>
  </svg>
  <div class="footer-url">WWW.TALLOWICKHAULAWAY.EXAMPLE</div>
</main>
</body>
</html>
```